Travel Agency Website - Simple General

Need a 7 page simple design that is pretty repetitive. Need to be able to load quickly that is SEO optimized. Trying to give ideas on what they can do, be personal as we are local, but at the same time come across as professional and get information easily with little burden.

- Landing Page
- Brimwell Vacations Page
- Family Trips
- Road Trips from Texas
- Other Destinations
- About Us Page
- Contact Us Page

Target Market(s)

Families

Coding

Coded - Design and coding required

Number of Pages Required

5+ page

Colors

Designer to choose colors to be used in the design.

Requirements
Must have
• Like it to flow easily with our logo. Use that for colors, etc.

```html
<!DOCTYPE html>
<html lang="en">
<head>
<meta charset="utf-8">
<title>About Us | Meadowlark Lane Travel Co.</title>
<meta name="description" content="A local family travel agency helping your family wander without the stress of planning.">
<link href="https://fonts.googleapis.com/css2?family=Montserrat:wght@600;700;800&family=Inter:ital,wght@0,400;0,500;0,600;1,300;1,400&display=swap" rel="stylesheet">
<style>
:root{
  --ink:#0b0f1e;
  --card:#121729;
  --card-line:#222a40;
  --gold:#d4a55a;
  --gold-deep:#c9994c;
  --white:#ffffff;
  --muted:#b7bccb;
  --footer:#1f3560;
  --footer-line:#30497a;
  --chip:#2b4472;
}
*{box-sizing:border-box;margin:0;padding:0}
html,body{width:1200px;height:2925px;overflow:hidden}
body{background:var(--ink);color:var(--white);font-family:"Inter",sans-serif;position:relative}
a{color:inherit;text-decoration:none}
.eyebrow{font-family:"Montserrat",sans-serif;font-weight:700;font-size:10px;letter-spacing:5px;color:var(--gold);text-transform:uppercase;display:flex;align-items:center;gap:6px}
.eyebrow svg{width:14px;height:14px;stroke:var(--gold);fill:none;stroke-width:2}
.rule{width:60px;height:3px;background:var(--gold);border-radius:2px}

/* header */
.site-header{position:absolute;top:0;left:0;width:1200px;height:78px;z-index:3}
.brand{position:absolute;left:119px;top:13px;width:58px;height:53px;background:#f3f4ef;display:flex;align-items:center;justify-content:center;text-align:center;font-weight:600;font-size:9px;line-height:1.1;color:#3f7d7a}
.main-nav{position:absolute;left:259px;top:31px;display:flex;gap:31px;font-size:11.5px;font-weight:600}
.main-nav .current{color:var(--gold)}
.btn-plan{position:absolute;left:927px;top:25px;width:154px;height:28px;border-radius:6px;background:var(--gold);color:#1b1608;font-family:"Montserrat",sans-serif;font-weight:700;font-size:11px;letter-spacing:.5px;display:flex;align-items:center;justify-content:center}

/* hero */
.hero{position:absolute;top:0;left:0;width:1200px;height:568px;background:
  linear-gradient(180deg,rgba(11,15,30,.35) 0%,rgba(11,15,30,0) 30%,rgba(11,15,30,.4) 70%,var(--ink) 100%),
  linear-gradient(180deg,#3a4f72 0%,#5c7396 28%,#2e3b3f 55%,#1f2a22 80%,#121a1c 100%)}
.hero-inner{position:absolute;top:144px;width:100%;text-align:center}
.hero .eyebrow{justify-content:center}
.hero h1{font-family:"Montserrat",sans-serif;font-weight:800;font-size:94px;line-height:1;color:var(--gold);margin-top:22px;letter-spacing:-1px}
.hero .tagline{font-style:italic;font-weight:300;font-size:18.5px;margin-top:28px;color:#e6e8ee}
.scroll-cue{position:absolute;top:518px;width:100%;text-align:center;font-size:8px;letter-spacing:3.5px;color:var(--gold-deep);font-weight:500}
.scroll-cue svg{display:block;margin:6px auto 0;width:14px;height:14px;stroke:var(--gold);fill:none;stroke-width:2}

/* story */
.story-photo{position:absolute;left:125px;top:681px;width:450px;height:467px;border-radius:42px;
  background:linear-gradient(180deg,#cfae8c 0%,#b98a58 50%,#6e4a22 78%,#1c160f 100%);
  box-shadow:0 24px 50px rgba(0,0,0,.45)}
.story-copy{position:absolute;left:625px;top:737px;width:455px}
.story-copy h2{font-family:"Montserrat",sans-serif;font-weight:700;font-size:48px;margin-top:26px}
.story-copy .rule{margin-top:26px}
.story-copy p{font-style:italic;font-weight:300;font-size:16.5px;line-height:25.5px;color:#c9cdd8;margin-top:30px}
.story-copy p+p{margin-top:25px}

/* values */
.values{position:absolute;top:1347px;left:0;width:1200px;text-align:center}
.values .eyebrow{justify-content:center;color:var(--white)}
.values h2{font-family:"Montserrat",sans-serif;font-weight:700;font-size:48px;margin-top:16px}
.values .rule{margin:18px auto 0}
.value-grid{position:absolute;top:165px;left:125px;display:flex;gap:25px}
.value-card{width:300px;height:256px;border-radius:34px;background:var(--card);border:1px solid var(--card-line);padding-top:37px}
.value-icon{width:62px;height:62px;margin:0 auto;border-radius:12px;background:#3a3226;border:1px solid #4d4230;display:flex;align-items:center;justify-content:center}
.value-icon svg{width:22px;height:22px;stroke:var(--gold);fill:none;stroke-width:2;stroke-linecap:round;stroke-linejoin:round}
.value-card h3{font-family:"Montserrat",sans-serif;font-weight:700;font-size:19px;margin-top:30px}
.value-card p{font-size:14.5px;line-height:23px;color:var(--muted);margin:20px auto 0;width:230px}

/* cta */
.cta{position:absolute;top:1869px;left:0;width:1200px;height:789px;
  background:linear-gradient(180deg,#1f2f4d 0%,#44577a 22%,#31405a 42%,#1d2b24 68%,#16211a 100%)}
.cta-card{position:absolute;left:251px;top:125px;width:698px;height:539px;border-radius:48px;text-align:center;
  background:linear-gradient(180deg,rgba(90,105,130,.6) 0%,rgba(70,80,95,.55) 55%,rgba(60,55,45,.6) 100%);
  border:1px solid rgba(255,255,255,.14);box-shadow:0 30px 60px rgba(0,0,0,.35)}
.cta-card .eyebrow{justify-content:center;margin-top:78px}
.cta-card h2{font-family:"Montserrat",sans-serif;font-weight:700;font-size:62px;line-height:70px;margin-top:30px}
.cta-card h2 span{color:var(--gold)}
.cta-card .rule{margin:32px auto 0}
.btn-story{display:flex;align-items:center;justify-content:center;gap:14px;margin:38px auto 0;width:349px;height:62px;border-radius:8px;background:var(--gold);color:#1b1608;font-family:"Montserrat",sans-serif;font-weight:700;font-size:19px;letter-spacing:2.5px;box-shadow:0 10px 26px rgba(0,0,0,.3)}
.btn-story svg{width:16px;height:16px;stroke:#1b1608;fill:none;stroke-width:2.5}

/* footer */
.site-footer{position:absolute;top:2658px;left:0;width:1200px;height:267px;background:var(--footer)}
.footer-brand{position:absolute;left:125px;top:50px;width:62px;height:57px;background:#f3f4ef;display:flex;align-items:center;justify-content:center;text-align:center;font-weight:600;font-size:9px;line-height:1.1;color:#3f7d7a}
.footer-about{position:absolute;left:125px;top:126px;width:210px;font-size:11px;line-height:17.5px}
.footer-col{position:absolute;top:52px}
.footer-col h4{font-family:"Montserrat",sans-serif;font-weight:700;font-size:15px}
.footer-col ul{list-style:none;margin-top:22px}
.footer-col li{font-size:11px;height:31.5px;color:#dfe4ee}
.contact-row{display:flex;align-items:center;gap:10px;font-size:11px;height:28px;color:#dfe4ee}
.contact-row svg{width:14px;height:14px;stroke:var(--gold);fill:none;stroke-width:2}
.social{display:flex;gap:10px;margin-top:14px}
.social a{height:26px;padding:0 10px;border-radius:13px;background:var(--chip);display:flex;align-items:center;font-size:10.5px;font-weight:500;color:#fff}
.footer-base{position:absolute;left:125px;top:240px;width:950px;border-top:1px solid var(--footer-line);text-align:center;font-size:8.5px;color:#9aa6c0;padding-top:6px;letter-spacing:.4px}
</style>
</head>
<body>

<header class="site-header">
  <a class="brand" href="#">Meadowlark Lane</a>
  <nav class="main-nav">
    <a href="#">Home</a><a href="#">Brimwell Vacations</a><a href="#">Family Trips</a><a href="#">Texas Road Trips</a><a href="#">Other Destinations</a><a class="current" href="#">About Us</a>
  </nav>
  <a class="btn-plan" href="#">START PLANNING</a>
</header>

<section class="hero" role="img" aria-label="Mountain valley with snowy peaks and evergreen forest">
  <div class="hero-inner">
    <div class="eyebrow"><svg viewBox="0 0 24 24"><path d="M12 3l1.8 5.2L19 10l-5.2 1.8L12 17l-1.8-5.2L5 10l5.2-1.8z"/></svg>Our Journey &amp; Mission</div>
    <h1>About Us</h1>
    <p class="tagline">"A local family dedicated to helping your family wander."</p>
  </div>
  <div class="scroll-cue">OUR STORY BELOW<svg viewBox="0 0 24 24"><path d="M6 9l6 6 6-6"/></svg></div>
</section>

<div class="story-photo" role="img" aria-label="Photo of a family in silhouette on a hilltop at a hazy golden sunrise"></div>
<section class="story-copy">
  <div class="eyebrow"><svg viewBox="0 0 24 24"><path d="M12 20s-7-4.5-7-10a4 4 0 0 1 7-2.5A4 4 0 0 1 19 10c0 5.5-7 10-7 10z"/></svg>Since the Beginning</div>
  <h2>Our Story</h2>
  <div class="rule"></div>
  <p>Meadowlark Lane started with a simple passion: helping our own friends and family experience the magic of travel without the overwhelming stress of planning.</p>
  <p>As a local, family-owned agency, we understand that vacations aren't just about the destination—they're about the moments spent together. We treat every itinerary as if it were for our own children and grandparents.</p>
</section>

<section class="values">
  <div class="eyebrow"><svg viewBox="0 0 24 24"><path d="M12 3l2.7 5.6 6.1.8-4.4 4.3 1 6.1L12 17l-5.4 2.8 1-6.1-4.4-4.3 6.1-.8z"/></svg>Our North Star</div>
  <h2>Our Values</h2>
  <div class="rule"></div>
  <div class="value-grid">
    <article class="value-card">
      <div class="value-icon"><svg viewBox="0 0 24 24"><path d="M12 20s-7-4.5-7-10a4 4 0 0 1 7-2.5A4 4 0 0 1 19 10c0 5.5-7 10-7 10z"/></svg></div>
      <h3>We Care</h3>
      <p>Your happiness is our primary metric. We go the extra mile.</p>
    </article>
    <article class="value-card">
      <div class="value-icon"><svg viewBox="0 0 24 24"><circle cx="9" cy="8" r="3.5"/><path d="M3 20c0-3.5 2.7-6 6-6s6 2.5 6 6"/><path d="M15 4.6a3.5 3.5 0 0 1 0 6.8M18 14.5c1.8.8 3 2.8 3 5.5"/></svg></div>
      <h3>Family First</h3>
      <p>Every recommendation is vetted for family safety and fun.</p>
    </article>
    <article class="value-card">
      <div class="value-icon"><svg viewBox="0 0 24 24"><path d="M12 3l2.7 5.6 6.1.8-4.4 4.3 1 6.1L12 17l-5.4 2.8 1-6.1-4.4-4.3 6.1-.8z"/></svg></div>
      <h3>Zero Fees</h3>
      <p>We are paid by suppliers, so our services are 100% free for you.</p>
    </article>
  </div>
</section>

<section class="cta" role="img" aria-label="Mountain range under a cloudy blue sky above a pine forest">
  <div class="cta-card">
    <div class="eyebrow"><svg viewBox="0 0 24 24"><path d="M12 3l1.8 5.2L19 10l-5.2 1.8L12 17l-1.8-5.2L5 10l5.2-1.8z"/></svg>Start Your Chapter</div>
    <h2>Let's Plan<br>Something<br><span>Together</span></h2>
    <div class="rule"></div>
    <a class="btn-story" href="#">START YOUR STORY <svg viewBox="0 0 24 24"><path d="M5 12h14M13 6l6 6-6 6"/></svg></a>
  </div>
</section>

<footer class="site-footer">
  <div class="footer-brand">Meadowlark Lane</div>
  <p class="footer-about">Making family memories easier with personalized, stress-free travel planning. Your local experts for magical vacations.</p>
  <div class="footer-col" style="left:372px">
    <h4>Quick Links</h4>
    <ul><li>Home</li><li>Brimwell Vacations</li><li>Family Trips</li><li>Texas Road Trips</li></ul>
  </div>
  <div class="footer-col" style="left:619px">
    <h4>Explore</h4>
    <ul><li>Other Destinations</li><li>About Us</li><li>Contact Us</li></ul>
  </div>
  <div class="footer-col" style="left:865px">
    <h4>Get in Touch</h4>
    <div style="margin-top:14px">
      <div class="contact-row"><svg viewBox="0 0 24 24"><path d="M5 3h4l2 5-2.5 1.5a11 11 0 0 0 6 6L16 13l5 2v4a2 2 0 0 1-2 2A16 16 0 0 1 3 5a2 2 0 0 1 2-2z"/></svg>555.010.2040</div>
      <div class="contact-row"><svg viewBox="0 0 24 24"><rect x="3" y="5" width="18" height="14" rx="2"/><path d="M3 7l9 6 9-6"/></svg>hello@meadowlarklane.com</div>
    </div>
    <div class="social"><a href="#">Circlet</a><a href="#">Snapfold</a></div>
  </div>
  <div class="footer-base">© 2026 Meadowlark Lane Travel Co. All rights reserved.</div>
</footer>

</body>
</html>
```